Dietitian needs awesome business card

I need a contemporary design that's eye catching but professional.
My card is to given to doctors, specialists and patients alike.
I manage patients with chronic diseases
I have uploaded my logo and current business card, I would also like the other Certified Clinical Nutritionist logo incorporated into the design

Target Market(s)

Doctors, specialists and patients

Industry/Entity Type

Healthcare

Contact Information for Business Card

www.brightfieldnutrition.com.au
Ph: 0427 561 903
Fax: 6457 2183
email: marcus.k.diet@fernmail.com
Space on the back of the card with: Appointment date, Appointment time and appointment location

Font styles to use
Serif

Colors
fbee3e
876aae
ffc214

Requirements
Must have
• My Logo
• Certified Clinical Nutritionist Logo
• My 4 locations - Pinebrook Medical Centre, North Corrin Health, Hollis Medical, Ashcombe Doctors Surgery
Nice to have
• I like the colours in my current business card

```html
<!DOCTYPE html>
<html lang="en">
<head>
<meta charset="utf-8">
<title>Brightfield Nutrition &amp; Dietetics – Business Card</title>
<link rel="stylesheet" href="https://fonts.googleapis.com/css2?family=Source+Sans+3:ital,wght@0,400;0,600;1,400&display=swap">
<style>
  :root {
    --backdrop: #2a2a2a;
    --card: #ffffff;
    --navy: #1f3a8f;
    --blue: #1677c8;
    --deep-blue: #1b2b86;
    --green: #8cc63f;
    --lime: #b6d433;
    --ink: #3a3a3a;
    --rule: #c9c9d2;
    --badge: #f47a20;
  }
  * { box-sizing: border-box; margin: 0; padding: 0; }
  html, body { width: 1200px; height: 987px; overflow: hidden; }
  body {
    background: var(--backdrop);
    font-family: "Source Sans 3", sans-serif;
    position: relative;
  }
  .card {
    position: absolute;
    left: 293px;
    width: 615px;
    height: 352px;
    background: var(--card);
    overflow: hidden;
  }
  .card--front { top: 130px; }
  .card--back { top: 505px; }

  .brand { position: absolute; display: flex; align-items: center; gap: 10px; color: var(--navy); }
  .brand__dot { width: 64px; height: 64px; border-radius: 50%; background: var(--green); flex: none; }
  .brand__name { font-weight: 400; line-height: 1.05; }
  .brand__name span { display: block; }
  .brand__name .brand__main { font-size: 36px; }
  .brand__name .brand__sub { font-size: 17px; }

  .card--front .brand { right: 34px; top: 38px; }
  .card--back .brand { left: 150px; top: 50px; }
  .card--back .brand__dot { width: 84px; height: 84px; }
  .card--back .brand__main { font-size: 42px; }
  .card--back .brand__sub { font-size: 19px; }

  .person { position: absolute; left: 26px; top: 146px; }
  .person__name { font-size: 23px; font-weight: 600; color: var(--navy); }
  .person__role { font-size: 17px; color: var(--green); margin-top: 2px; }

  .badge {
    position: absolute; left: 507px; top: 158px;
    width: 74px; height: 35px; border-radius: 3px; background: var(--badge);
  }
  .divider { position: absolute; left: 26px; right: 34px; top: 225px; height: 1px; background: var(--rule); }

  .contacts { position: absolute; left: 26px; top: 238px; list-style: none; }
  .contacts li { display: flex; align-items: center; gap: 7px; font-size: 16.5px; color: var(--ink); height: 23.5px; }
  .contacts svg { width: 15px; height: 15px; fill: var(--navy); flex: none; }

  .swoosh { position: absolute; left: 0; bottom: 0; width: 615px; height: 46px; }
  .swoosh__url {
    position: absolute; right: 26px; bottom: 12px;
    font-size: 17px; font-style: italic; color: #fff;
  }

  .appt { position: absolute; left: 40px; right: 42px; color: var(--navy); font-size: 17px; display: flex; align-items: flex-end; gap: 6px; }
  .appt__line { flex: 1; border-bottom: 1px solid #8a93b8; height: 1px; margin-bottom: 5px; }
  .appt__line--short { flex: 0 0 118px; }
  .appt__gap { width: 8px; }
  .appt__unit { font-size: 13px; margin-bottom: 1px; }
  .appt--datetime { top: 208px; }
  .appt--location { top: 259px; }

  .back__url {
    position: absolute; left: 0; right: 0; top: 302px; text-align: center;
    font-size: 16px; font-style: italic; letter-spacing: 3.6px; color: #555;
  }
</style>
</head>
<body>

<section class="card card--front" aria-label="Business card front">
  <div class="brand">
    <span class="brand__dot"></span>
    <div class="brand__name"><span class="brand__main">Brightfield</span><span class="brand__sub">Nutrition &amp; Dietetics</span></div>
  </div>

  <div class="person">
    <p class="person__name">Marcus Kellaway</p>
    <p class="person__role">Nutritionist &amp; Chef</p>
  </div>

  <div class="badge" role="img" aria-label="Certified Clinical Nutritionist badge"></div>
  <div class="divider"></div>

  <ul class="contacts">
    <li><svg viewBox="0 0 16 16" aria-hidden="true"><path d="M3.5 1l2.3 2.7-1.3 2a8 8 0 0 0 5.8 5.8l2-1.3L15 12.5 13.2 15C6.5 14.6 1.4 9.5 1 2.8z"/></svg>0427 561 903</li>
    <li><svg viewBox="0 0 16 16" aria-hidden="true"><path d="M4 1h8v4H4zM1 6h14v6h-2v3H3v-3H1zm4 4v3h6v-3z"/></svg>6457 2183</li>
    <li><svg viewBox="0 0 16 16" aria-hidden="true"><path d="M1 3h14v10H1zm1.5 1.3L8 8.6l5.5-4.3z" /></svg>marcus.k.diet@fernmail.com</li>
  </ul>

  <svg class="swoosh" viewBox="0 0 615 46" preserveAspectRatio="none" aria-hidden="true">
    <defs>
      <linearGradient id="greenBand" x1="0" x2="1">
        <stop offset="0" stop-color="var(--green)"/>
        <stop offset="1" stop-color="var(--lime)"/>
      </linearGradient>
      <linearGradient id="blueBand" x1="0" x2="1">
        <stop offset="0" stop-color="var(--blue)"/>
        <stop offset="1" stop-color="var(--deep-blue)"/>
      </linearGradient>
    </defs>
    <rect x="0" y="24" width="615" height="22" fill="var(--deep-blue)"/>
    <path d="M0 18 H340 Q356 18 362 22 L362 28 H0 Z" fill="url(#greenBand)"/>
    <path d="M0 28 H360 Q368 28 372 20 Q380 4 398 4 H615 V46 H0 Z" fill="url(#blueBand)"/>
  </svg>
  <span class="swoosh__url">brightfieldnutrition.com.au</span>
</section>

<section class="card card--back" aria-label="Business card back">
  <div class="brand">
    <span class="brand__dot"></span>
    <div class="brand__name"><span class="brand__main">Brightfield</span><span class="brand__sub">Nutrition &amp; Dietetics</span></div>
  </div>

  <div class="appt appt--datetime">
    <span>Date :</span><span class="appt__line"></span><span class="appt__gap"></span>
    <span>Time :</span><span class="appt__line appt__line--short"></span><span class="appt__unit">AM/PM</span>
  </div>
  <div class="appt appt--location">
    <span>Location :</span><span class="appt__line"></span>
  </div>

  <p class="back__url">www.brightfieldnutrition.com.au</p>
</section>

</body>
</html>
```